3 Business Card designs for a company with multiple services

We are a company that has 3 main services:

1) Security - CCTV & Alarm Sepcialists
2) Broadcast - Broadcast Sales and Technical Services
3) Distribution - Quality Products, Quality Service

The broadcast service is for Video Broadcast.

I will include our logos for each service.

I would like to also create a business card design for 7QR in general (see main logo).

Each card will be two-sided. On the front I would think it would include Logo, Name, Posistion and Mobile (and possibly email). And possibly our main number (which may be something like 1800 639 415)

On the back it MUST include a "lined" section to be able to write short quotes / prices.

Then include more details like Phone: 1800 639 415 Fax: 1800 639 417 Postal: PO Box 917, Tallowfield, QLD Australia 4287 Website: www.7qr.com.au

We would like a fresh, inovative card design with that "wow check this out" feel about it.

Look forward to seeing what you can do! :)

Corin

• Quote section on the back!
Editable files.

```html
<!DOCTYPE html>
<html lang="en">
<head>
<meta charset="utf-8">
<title>7QR Business Cards</title>
<link rel="stylesheet" href="https://fonts.googleapis.com/css2?family=Source+Sans+3:wght@400;600;700&display=swap">
<style>
  :root {
    --stage: #000;
    --red-top: #e4232c;
    --red-bottom: #a40f1b;
    --amber-top: #f9b800;
    --amber-bottom: #e58a1c;
    --dark-top: #3b3b3d;
    --dark-bottom: #141415;
    --strip: #1b1b1c;
    --white: #ffffff;
    --ink: #111;
    --rule: #d6d6d6;
    --logo-bg: #1e1e20;
    --security: #c4161c;
    --distribution: #f2a20c;
  }
  * { box-sizing: border-box; margin: 0; padding: 0; }
  html, body { width: 1200px; height: 900px; overflow: hidden; }
  body {
    background: var(--stage);
    font-family: "Source Sans 3", Arial, sans-serif;
    color: var(--white);
    position: relative;
  }
  .card {
    position: absolute;
    top: 214px;
    width: 252px;
    height: 442px;
    border-radius: 10px;
    overflow: hidden;
    background: linear-gradient(180deg, var(--dark-top), var(--dark-bottom));
  }
  .card--security-front { left: 52px; }
  .card--security-back { left: 332px; }
  .card--distribution-front { left: 614px; }
  .card--distribution-back { left: 896px; }

  .card-face { position: absolute; left: 0; top: 0; width: 100%; height: 416px; }
  .card--security-front .card-face { background: linear-gradient(180deg, var(--red-top), var(--red-bottom)); }
  .card--distribution-front .card-face { background: linear-gradient(180deg, var(--amber-top), var(--amber-bottom)); }
  .card-face svg { position: absolute; inset: 0; width: 100%; height: 100%; }
  .card-strip { position: absolute; left: 0; bottom: 0; width: 100%; height: 26px; background: var(--strip); }

  .brand {
    position: absolute; left: 36px; top: 22px; width: 184px; height: 58px;
    border-radius: 5px;
    background: var(--logo-bg);
    border: 2px solid #d9d9d9;
    display: flex; align-items: center; gap: 10px; padding: 0 12px;
  }
  .brand-mark { width: 30px; height: 30px; border-radius: 4px; flex: none; }
  .card--security-front .brand-mark, .card--security-back .brand-mark { background: var(--security); }
  .card--distribution-front .brand-mark, .card--distribution-back .brand-mark { background: var(--distribution); }
  .brand-text { display: flex; flex-direction: column; line-height: 1; color: var(--white); font-weight: 700; }
  .brand-name { font-size: 26px; letter-spacing: 6px; }
  .brand-service { font-size: 11px; letter-spacing: 2px; margin-top: 3px; }

  .person { position: absolute; left: 18px; top: 306px; }
  .person-name { font-size: 21px; font-weight: 700; line-height: 1.1; }
  .person-role { font-size: 13px; margin-top: 4px; }
  .contact-list { list-style: none; margin-top: 16px; font-size: 10px; line-height: 15px; }
  .contact-list li { display: flex; align-items: center; gap: 6px; }
  .contact-list svg { width: 9px; height: 9px; fill: var(--white); flex: none; }

  .note {
    position: absolute; left: 28px; top: 100px; width: 202px; height: 232px;
    background: var(--white); border-radius: 8px; color: var(--ink);
    padding: 8px 12px;
  }
  .note-label { font-size: 12px; font-weight: 700; line-height: 16px; }
  .note-lines {
    position: absolute; left: 12px; right: 12px; top: 30px; bottom: 14px;
    background: repeating-linear-gradient(180deg, transparent 0 21px, var(--rule) 21px 22px);
  }
  .back-badge { position: absolute; left: 184px; top: 294px; width: 46px; height: 48px; }
  .back-badge--security { background: var(--security); border-radius: 6px; }
  .back-badge--distribution { background: var(--distribution); border-radius: 50%; border: 2px solid var(--white); top: 298px; height: 46px; }
  .back-details { position: absolute; left: 28px; top: 352px; font-size: 10px; line-height: 14px; font-style: normal; }
</style>
</head>
<body>

<article class="card card--security-front">
  <div class="card-face">
    <svg viewBox="0 0 252 416" preserveAspectRatio="none" aria-hidden="true">
      <path d="M0 150 C80 60 180 60 252 110 L252 0 L0 0 Z" fill="#ffffff" opacity="0.06"/>
      <path d="M0 240 C90 170 170 150 252 160 L252 0 L0 0 Z" fill="#ffffff" opacity="0.05"/>
    </svg>
  </div>
  <div class="card-strip"></div>
  <div class="brand">
    <span class="brand-mark"></span>
    <span class="brand-text"><span class="brand-name">7QR</span><span class="brand-service">SECURITY</span></span>
  </div>
  <div class="person">
    <h2 class="person-name">Alex Marlow</h2>
    <p class="person-role">Field Manager</p>
    <ul class="contact-list">
      <li><svg viewBox="0 0 10 10"><rect x="3" y="0" width="4" height="10" rx="1"/></svg>200 481 5530</li>
      <li><svg viewBox="0 0 10 10"><path d="M0 3 Q5 -1 10 3 L8 5 L6 3 H4 L2 5 Z M2 6 H8 V10 H2 Z"/></svg>1800 639 415</li>
      <li><svg viewBox="0 0 10 10"><path d="M0 2 H10 V8 H0 Z M0 2 L5 6 L10 2" fill="none" stroke="#fff"/></svg>alex@7qr.com.au</li>
    </ul>
  </div>
</article>

<article class="card card--security-back">
  <div class="brand">
    <span class="brand-mark"></span>
    <span class="brand-text"><span class="brand-name">7QR</span><span class="brand-service">SECURITY</span></span>
  </div>
  <div class="note">
    <p class="note-label">Note :</p>
    <div class="note-lines"></div>
  </div>
  <div class="back-badge back-badge--security"></div>
  <address class="back-details">
    Phone: 1800 639 415<br>
    Fax: 1800 639 417<br>
    Postal: PO Box 917, Tallowfield<br>
    QLD Australia 4287
  </address>
</article>

<article class="card card--distribution-front">
  <div class="card-face">
    <svg viewBox="0 0 252 416" preserveAspectRatio="none" aria-hidden="true">
      <path d="M0 150 C80 60 180 60 252 110 L252 0 L0 0 Z" fill="#ffffff" opacity="0.10"/>
      <path d="M0 240 C90 170 170 150 252 160 L252 0 L0 0 Z" fill="#ffffff" opacity="0.07"/>
    </svg>
  </div>
  <div class="card-strip"></div>
  <div class="brand">
    <span class="brand-mark"></span>
    <span class="brand-text"><span class="brand-name">7QR</span><span class="brand-service">DISTRIBUTION</span></span>
  </div>
  <div class="person">
    <h2 class="person-name">Alex Marlow</h2>
    <p class="person-role">Field Manager</p>
    <ul class="contact-list">
      <li><svg viewBox="0 0 10 10"><rect x="3" y="0" width="4" height="10" rx="1"/></svg>200 481 5530</li>
      <li><svg viewBox="0 0 10 10"><path d="M0 3 Q5 -1 10 3 L8 5 L6 3 H4 L2 5 Z M2 6 H8 V10 H2 Z"/></svg>1800 639 415</li>
      <li><svg viewBox="0 0 10 10"><path d="M0 2 H10 V8 H0 Z M0 2 L5 6 L10 2" fill="none" stroke="#fff"/></svg>alex@7qr.com.au</li>
    </ul>
  </div>
</article>

<article class="card card--distribution-back">
  <div class="brand">
    <span class="brand-mark"></span>
    <span class="brand-text"><span class="brand-name">7QR</span><span class="brand-service">DISTRIBUTION</span></span>
  </div>
  <div class="note">
    <p class="note-label">Note :</p>
    <div class="note-lines"></div>
  </div>
  <div class="back-badge back-badge--distribution"></div>
  <address class="back-details">
    Phone: 1800 639 415<br>
    Fax: 1800 639 417<br>
    Postal: PO Box 917, Tallowfield<br>
    QLD Australia 4287
  </address>
</article>

</body>
</html>
```